PAX

We need to design a power point presentation that can englobe all our company products.

This presentation has to have all the required to be used as template for future presentations.

We focus on prodcut developing for supermarkets, ( we help them with their own brand products ex. Sunny Harvest, TK, etc.)
Also we are on the marine industry, we develop ships and oil rigs for the Oil and deep water market.

Target Market(s)

Oil Companies
Supermarket companies
Retail Companies

Industry/Entity Type

It Company

Requirements
Must have
• Our Logo and company colors
Nice to have
• Something describing globalization.
Should not have
• Orange color

```html
<!DOCTYPE html>
<html lang="en">
<head>
<meta charset="utf-8">
<title>PAX – Corporate Overview</title>
<link href="https://fonts.googleapis.com/css2?family=Open+Sans:wght@300;400;600;700;800&display=swap" rel="stylesheet">
<style>
  :root {
    --bg: #f5f5f5;
    --navy: #13275f;
    --blue: #1b8fd8;
    --sky: #36b6f0;
    --green: #7bc043;
    --text: #2f2f2f;
    --rule: #9a9a9a;
    --ocean: #1b6fb8;
    --ocean-mid: #6fb3e0;
    --ocean-pale: #c4e2f6;
    --purple: #6a1f7c;
    --purple-light: #a986bd;
    --olive: #64951f;
    --olive-light: #a9c77a;
    --panel: #ffffff;
  }
  * { margin: 0; padding: 0; box-sizing: border-box; }
  html, body { width: 1200px; height: 900px; overflow: hidden; }
  body {
    background: var(--bg);
    font-family: "Open Sans", Arial, sans-serif;
    color: var(--text);
    position: relative;
  }
  .page-title {
    position: absolute; left: 42px; top: 28px;
    font-size: 40px; font-weight: 300; color: var(--navy); letter-spacing: -0.3px;
  }
  .review-tag {
    position: absolute; right: 45px; top: 48px;
    font-size: 20px; font-weight: 300; color: var(--green);
  }
  .review-tag b { color: var(--sky); font-weight: 700; }
  .header-rule { position: absolute; left: 42px; top: 82px; }

  .corner-glow {
    position: absolute; left: 0; top: 670px; width: 480px; height: 230px;
    background:
      radial-gradient(ellipse at 0% 30%, rgba(123,192,67,0.55) 0%, rgba(123,192,67,0) 45%),
      radial-gradient(ellipse at 35% 100%, rgba(54,182,240,0.45) 0%, rgba(54,182,240,0) 60%);
  }

  .intro { position: absolute; left: 45px; top: 133px; width: 410px; }
  .intro h1 {
    font-size: 39px; line-height: 40px; font-weight: 800; color: var(--navy); letter-spacing: 0.3px;
  }
  .intro .lead {
    margin-top: 22px; font-size: 15.6px; line-height: 23.5px; font-weight: 300; color: var(--text);
    letter-spacing: -0.1px; hyphens: auto;
  }
  .divider { position: absolute; left: 45px; top: 403px; width: 391px; border-top: 1px solid var(--rule); }

  .sections { position: absolute; left: 45px; top: 418px; width: 395px; }
  .sections h2 { font-size: 11.5px; font-weight: 700; color: var(--text); margin-bottom: 6px; }
  .sections p {
    font-size: 11.2px; line-height: 14.6px; font-weight: 300; margin-bottom: 18px;
    letter-spacing: -0.1px; hyphens: auto;
  }

  .countries { position: absolute; left: 550px; top: 133px; }
  .countries h2 { font-size: 26px; line-height: 30px; font-weight: 700; color: var(--navy); letter-spacing: 0.5px; }
  .countries .count {
    font-size: 122px; line-height: 110px; font-weight: 300; color: var(--blue); margin-top: 4px; letter-spacing: -4px;
  }
  .country-list {
    position: absolute; left: 549px; top: 335px; width: 170px;
    display: grid; grid-template-columns: 92px 80px; grid-auto-flow: column; grid-template-rows: repeat(13, 14.6px);
    font-size: 10.5px; font-weight: 600; color: var(--text); list-style: none;
  }
  .world-map { position: absolute; left: 730px; top: 262px; width: 425px; height: 262px; }
  .map-fill {
    position: absolute; inset: 0; border-radius: 40px;
    background: radial-gradient(ellipse at center, #d2d2d2 0%, #dcdcdc 55%, rgba(245,245,245,0) 78%);
  }
  .map-label {
    position: absolute; font-size: 11px; line-height: 12px; font-weight: 700; color: var(--blue); white-space: nowrap;
  }

  .passages {
    position: absolute; left: 549px; top: 583px; width: 606px; height: 267px; background: var(--panel);
  }
  .passages h2 {
    position: absolute; left: 23px; top: 33px; font-size: 14px; line-height: 17px; font-weight: 700; color: var(--navy);
  }
  .passages .vrule { position: absolute; left: 125px; top: 32px; height: 205px; border-left: 1px solid var(--rule); }
  .chart { position: absolute; top: 34px; width: 145px; }
  .chart h3 { font-size: 8.5px; line-height: 10.5px; font-weight: 700; color: var(--navy); height: 34px; }
  .chart svg { display: block; }
  .legend { list-style: none; margin-top: 16px; font-size: 10px; line-height: 10.5px; }
  .legend li { display: flex; gap: 6px; margin-bottom: 2px; }
  .legend i { flex: none; width: 8px; height: 8px; margin-top: 1px; }

  .brand {
    position: absolute; left: 45px; top: 804px; display: flex; align-items: center; gap: 10px;
  }
  .brand .dot { width: 30px; height: 30px; border-radius: 50%; background: var(--blue); }
  .brand span { font-size: 28px; font-weight: 700; color: var(--green); letter-spacing: 1px; }
</style>
</head>
<body>
  <div class="corner-glow" role="img" aria-label="Soft green and blue light glow suggesting global reach"></div>

  <div class="page-title">Corporate Overview</div>
  <div class="review-tag">STRATEGIC REVIEW <b>2014</b></div>
  <svg class="header-rule" width="1114" height="14" viewBox="0 0 1114 14">
    <polyline points="0,3 6,3 14,10 22,3 1114,3" fill="none" stroke="#36b6f0" stroke-width="1"/>
  </svg>

  <section class="intro">
    <h1>LOREM IPSUM<br>IS SIMPLY<br>DUMMY TEXT</h1>
    <p class="lead">Lorem Ipsum is simply dummy text of the printing and typesetting industry. Lorem Ipsum has been the indus&shy;try's standard dummy text ever since the 1500s, when an unknown printer took a galley of type and scrambled it to make a type specimen book.</p>
  </section>
  <div class="divider"></div>

  <section class="sections">
    <h2>OUR MISSION</h2>
    <p>Lorem Ipsum is simply dummy text of the printing and typesetting industry. Lorem Ipsum has been the industry's nchanged. It was popularised in the 1960s with the release of Tyneset sheets containing standard dummy text ever since the 1500s, when an unknown printer.</p>
    <h2>PAX 2014</h2>
    <p>It has survived not only five centuries, but also the leap into electronic type&shy;setting, remaining essentially unchanged. It was popularised in the 1960s with the release of Tyneset sheets containing &nbsp;only five centuries, but also the leap into electronic typesetting, remaining essentially unchanged. It was popular&shy;ised in the 1960s with the release of Tyneset sheets containing</p>
    <h2>LOREM IPSUM</h2>
    <p>It Lorem Ipsum passages, and more recently with desktop publishing software like Folio PageCraft including versions of Lorem Ipsum. essentially un&shy;changed. It was popularised in the 1960s with the release of Tyneset sheets containing</p>
  </section>

  <section class="countries">
    <h2>OUR COUNTRIES<br>WORLDWIDE</h2>
    <div class="count">33</div>
  </section>
  <ul class="country-list">
    <li>Italy</li><li>Japan</li><li>Korea, North</li><li>Luxembourg</li><li>Mexico</li><li>Malaysia</li><li>Netherlands</li><li>New Zealand</li><li>Philippines</li><li>Poland</li><li>Portugal</li><li>Russia</li><li>United Kingdom</li>
    <li>Denmark</li><li>Argentina</li><li>Australia</li><li>Austria</li><li>Canada</li><li>Finland</li><li>France</li><li>Germany</li><li>Hong Kong</li><li>India</li><li>Indonesia</li><li>Ireland</li>
  </ul>

  <div class="world-map">
    <div class="map-fill" role="img" aria-label="Grey world map showing the continents"></div>
  </div>
  <svg width="1200" height="900" style="position:absolute;left:0;top:0;pointer-events:none">
    <g fill="none" stroke="#1b8fd8">
      <line x1="984" y1="282" x2="969" y2="330" stroke-width="1.5"/>
      <line x1="834" y1="375" x2="815" y2="418" stroke-width="1.5"/>
      <line x1="1096" y1="459" x2="1090" y2="488" stroke-width="1.5"/>
      <circle cx="965" cy="338" r="9.5" stroke-width="4"/>
      <circle cx="838" cy="366" r="9.5" stroke-width="4"/>
      <circle cx="1098" cy="450" r="9.5" stroke-width="4"/>
    </g>
  </svg>
  <div class="map-label" style="left:970px;top:247px">ST PETERSBURG<br>RUSSIA, 2014</div>
  <div class="map-label" style="left:749px;top:431px">DETROIT<br>UNITED STATES, 2014</div>
  <div class="map-label" style="left:1056px;top:491px">MACKAY<br>AUSTRALIA, 2012</div>

  <section class="passages">
    <h2>PASSAGES OF<br>LOREM 2014</h2>
    <div class="vrule"></div>

    <div class="chart" style="left:156px">
      <h3>NULLAM AUCTOR DUI<br>UT LEO (%)</h3>
      <svg width="110" height="110" viewBox="0 0 110 110" font-size="10" font-family="Open Sans, sans-serif">
        <g transform="rotate(-90 55 55)" fill="none" stroke-width="18">
          <circle cx="55" cy="55" r="45" pathLength="100" stroke="var(--ocean)" stroke-dasharray="40 60"/>
          <circle cx="55" cy="55" r="45" pathLength="100" stroke="var(--ocean-mid)" stroke-dasharray="0 40 31 29"/>
          <circle cx="55" cy="55" r="45" pathLength="100" stroke="var(--ocean-pale)" stroke-dasharray="0 71 29 0"/>
        </g>
        <text x="60" y="21" fill="#fff">40</text>
        <text x="71" y="98" fill="#fff">31</text>
        <text x="5" y="61" fill="#5aa2d4">29</text>
      </svg>
      <ul class="legend">
        <li><i style="background:var(--ocean)"></i>Sed molestie urna<br>et mattis tempor.</li>
        <li><i style="background:var(--ocean-mid)"></i>Morbi mattis</li>
        <li><i style="background:var(--ocean-pale)"></i>Duis congue quam</li>
      </ul>
    </div>

    <div class="chart" style="left:307px">
      <h3>ALIQUAM UT LOREM ET<br>ENIM FERMENTUM (%)</h3>
      <svg width="110" height="110" viewBox="0 0 110 110" font-size="10" font-family="Open Sans, sans-serif">
        <g transform="rotate(-90 55 55)" fill="none" stroke-width="18">
          <circle cx="55" cy="55" r="45" pathLength="100" stroke="var(--purple)" stroke-dasharray="59 41"/>
          <circle cx="55" cy="55" r="45" pathLength="100" stroke="var(--purple-light)" stroke-dasharray="0 59 41 0"/>
        </g>
        <text x="53" y="21" fill="#fff">59</text>
        <text x="18" y="95" fill="#fff">41</text>
      </svg>
      <ul class="legend">
        <li><i style="background:var(--purple)"></i>Mattis tempor.</li>
        <li><i style="background:var(--purple-light)"></i>Nec condimentum<br>suscipit.</li>
      </ul>
    </div>

    <div class="chart" style="left:447px">
      <h3>SED NON MI CONGUE, IACULIS<br>NEQUE AT (%)</h3>
      <svg width="120" height="110" viewBox="0 0 120 110" font-size="10" font-family="Open Sans, sans-serif">
        <g transform="rotate(-90 66 55)" fill="none" stroke-width="18">
          <circle cx="66" cy="55" r="45" pathLength="100" stroke="var(--olive)" stroke-dasharray="84 16"/>
          <circle cx="66" cy="55" r="45" pathLength="100" stroke="var(--olive-light)" stroke-dasharray="0 84 16 0"/>
        </g>
        <text x="72" y="21" fill="#fff">84</text>
        <text x="31" y="31" fill="#fff">16</text>
      </svg>
      <ul class="legend">
        <li><i style="background:var(--olive)"></i>Donec pharetra nisi</li>
        <li><i style="background:var(--olive-light)"></i>Tristique volutpat.</li>
      </ul>
    </div>
  </section>

  <div class="brand">
    <div class="dot"></div>
    <span>PAX</span>
  </div>
</body>
</html>
```